Specialised investor in e-mobility and energy wants business card design

We need a business card design that fits our existing corporate design. <The look and feel must be 'sharp'/'clean', dynamic, communicate momentum, professionalism etc (as one would imagine from a firm in the financial sector). We like the idea of a reverse-side of the card that includes the logo, and the name and contact details on the other. We expect the deliverable to be whatever format might be required to be able to get cards printed directly by a service such as kelmo press. Our website is www.zub.capital

```html
<!DOCTYPE html>
<html lang="en">
<head>
<meta charset="utf-8">
<title>ZUB Capital – Business Card</title>
<link href="https://fonts.googleapis.com/css2?family=Poppins:wght@400;500;600&display=swap" rel="stylesheet">
<style>
  :root {
    --bg: #d4d4d4;
    --paper: #ffffff;
    --green-dark: #2f5a22;
    --green-mid: #4d7c2f;
    --green-light: #8cb84c;
    --ink: #1f1f1f;
    --rule: #b9b9b9;
  }
  * { margin: 0; padding: 0; box-sizing: border-box; }
  html, body { width: 1200px; height: 800px; overflow: hidden; }
  body {
    background: var(--bg);
    font-family: "Poppins", sans-serif;
    display: flex;
    align-items: center;
    justify-content: center;
    gap: 60px;
  }
  .card {
    width: 525px;
    height: 300px;
    position: relative;
    box-shadow: 0 8px 24px rgba(0,0,0,0.18);
  }
  /* Front side */
  .card-front {
    background: var(--paper);
    display: flex;
    align-items: center;
  }
  .front-brand {
    width: 250px;
    display: flex;
    justify-content: center;
    align-items: center;
  }
  .brand-name {
    font-weight: 400;
    color: var(--green-dark);
    font-size: 34px;
    letter-spacing: 0.5px;
    white-space: nowrap;
  }
  .divider {
    width: 1px;
    height: 190px;
    background: linear-gradient(to bottom, transparent, var(--rule) 20%, var(--rule) 80%, transparent);
  }
  .front-details {
    padding-left: 30px;
    color: var(--ink);
  }
  .person-name {
    font-weight: 600;
    color: var(--green-dark);
    font-size: 19px;
    letter-spacing: 0.5px;
    line-height: 1.1;
  }
  .person-role {
    font-size: 13px;
    color: #333;
    margin-bottom: 14px;
  }
  .contact-list { list-style: none; font-size: 13px; line-height: 1.65; }
  .contact-list li { display: flex; align-items: center; gap: 8px; white-space: nowrap; }
  .contact-list svg { width: 12px; height: 12px; flex: none; }
  .icon-fill { fill: var(--green-dark); }
  .icon-line { fill: none; stroke: var(--green-dark); stroke-width: 2.2; }
  .contact-list .accent { color: var(--green-mid); }
  .address { font-size: 13px; line-height: 1.4; margin-top: 12px; padding-left: 20px; }

  /* Back side */
  .card-back {
    background: linear-gradient(200deg, var(--green-light) 0%, var(--green-mid) 45%, var(--green-dark) 100%);
    display: flex;
    flex-direction: column;
    align-items: center;
    justify-content: center;
    color: var(--paper);
  }
  .card-back .brand-name {
    color: var(--paper);
    font-size: 46px;
    margin-bottom: 40px;
  }
  .back-web {
    display: flex;
    align-items: center;
    gap: 12px;
    font-size: 15px;
    letter-spacing: 3px;
  }
  .back-web .line { width: 80px; height: 1px; background: rgba(255,255,255,0.8); }
</style>
</head>
<body>
  <section class="card card-front">
    <div class="front-brand">
      <span class="brand-name">ZUB Capital</span>
    </div>
    <div class="divider"></div>
    <div class="front-details">
      <h1 class="person-name">MARTEN HOLLOWAY</h1>
      <p class="person-role">Managing Director</p>
      <ul class="contact-list">
        <li>
          <svg viewBox="0 0 24 24"><path class="icon-fill" d="M6.6 10.8a15 15 0 006.6 6.6l2.2-2.2a1 1 0 011-.25 11.4 11.4 0 003.6.57 1 1 0 011 1V20a1 1 0 01-1 1A17 17 0 013 4a1 1 0 011-1h3.5a1 1 0 011 1c0 1.25.2 2.45.57 3.6a1 1 0 01-.25 1z"/></svg>
          <span>044-318 620 475</span>
        </li>
        <li>
          <svg viewBox="0 0 24 24"><rect class="icon-line" x="2" y="5" width="20" height="14"/><path class="icon-line" d="M2 5l10 8 10-8"/></svg>
          <span>info@zub.capital</span>
        </li>
        <li>
          <svg viewBox="0 0 24 24"><circle class="icon-line" cx="12" cy="12" r="10"/><path class="icon-line" d="M2 12h20M12 2c3 3 3 17 0 20M12 2c-3 3-3 17 0 20"/></svg>
          <span>www.<span class="accent">zub</span>.capital</span>
        </li>
      </ul>
      <p class="address">87, Ridgefield Lane, Suite 3<br>30918, Northvale</p>
    </div>
  </section>

  <section class="card card-back">
    <span class="brand-name">ZUB Capital</span>
    <div class="back-web">
      <span class="line"></span>
      <span>www.zub.capital</span>
      <span class="line"></span>
    </div>
  </section>
</body>
</html>
```